Business card design for a dynamic IT consulting company

We need a business card design for a young firm, specialized in the Telecommunications/Consulting industry. The name of the company is Quindor and Partners Business Consulting Ltd. (Short name: Quindor and Partnes)
Quindor = solve read reverse, so we aim to be uncomplicated and solution-oriented. The small pipe in our logo is also related to the word solve. So we need a new business card design, which is simple, eye catching and something non traditional (I would probably prefer a square shaped design rather than a rectangle, but open for suggestions). Attached our logo.

Target Market(s)

Usually our customers are Tier1 Telecoms providers (Q-Netra, Palorix, etc) and their executives.

Industry/Entity Type

Business

Contact Information for Business Card

Name: Bence Tolnavari
Email: b.tolnavari@quindor.hu
Web: www.quindor.hu
Mobile: +36 30 518 2769
Title: Managing Director

Optional:
Company name: Quindor and Partners Ltd.
Address: 1087 Budapest, Tolvenka str. 28/C, Hungary

Font styles to use
Other font styles liked:
• helveticaneue_medium, Prime Regular are used now.

Colors

Designer to choose colors to be used in the design.

Requirements
Must have
• I would like to have a 2 sided design.
Nice to have
• I thought if we make the logo a bit bigger (without the company name), that could go to the back with the company name below. I though, if the pipe in the logo is somehow touchable on the business card, would be nice and unique.

```html
<!DOCTYPE html>
<html lang="en">
<head>
<meta charset="utf-8">
<title>Quindor and Partners – Business Card</title>
<link rel="stylesheet" href="https://fonts.googleapis.com/css2?family=Montserrat:wght@600&family=Work+Sans:wght@300;400&display=swap">
<style>
  :root {
    --brand-blue: #1b9bd8;
    --brand-magenta: #b92d8f;
    --brand-grey: #5b5e60;
    --text-grey: #555a5d;
    --paper: #ffffff;
    --backdrop: #e9eaeb;
  }
  * { margin: 0; padding: 0; box-sizing: border-box; }
  html, body { width: 1200px; height: 930px; overflow: hidden; }
  body {
    position: relative;
    background: var(--backdrop);
    font-family: "Work Sans", sans-serif;
    color: var(--text-grey);
  }
  .card {
    position: absolute;
    left: 278px;
    width: 645px;
    height: 370px;
    overflow: hidden;
  }
  .card--front { top: 75px; background: var(--paper); }
  .card--back { top: 486px; background: var(--brand-blue); }

  .wordmark {
    position: absolute;
    display: flex;
    align-items: center;
    font-family: "Work Sans", sans-serif;
    font-weight: 400;
    white-space: nowrap;
  }
  .wordmark__square { display: block; }
  .card--front .wordmark { left: 33px; top: 40px; font-size: 22px; color: var(--brand-grey); gap: 10px; }
  .card--front .wordmark__square { width: 16px; height: 16px; background: var(--brand-blue); }
  .card--back .wordmark { left: 0; right: 0; top: 158px; justify-content: center; font-size: 44px; color: var(--paper); gap: 20px; }
  .card--back .wordmark__square { width: 34px; height: 34px; background: var(--paper); }

  .pattern-field {
    position: absolute;
    left: 370px;
    top: 0;
    width: 275px;
    height: 370px;
    background: linear-gradient(160deg, var(--brand-magenta) 0%, var(--brand-blue) 45%, var(--brand-grey) 75%, var(--brand-blue) 100%);
    opacity: 0.85;
  }

  .contact { position: absolute; left: 33px; top: 176px; }
  .contact__name {
    font-family: "Montserrat", sans-serif;
    font-weight: 600;
    font-size: 22px;
    letter-spacing: 0.3px;
    color: var(--brand-blue);
    line-height: 1.1;
  }
  .contact__title, .contact__address, .contact__line {
    font-weight: 300;
    font-size: 15.5px;
    line-height: 20px;
  }
  .contact__address { margin-top: 10px; }
  .contact__list { list-style: none; margin-top: 8px; }
  .contact__line { display: flex; align-items: center; gap: 10px; line-height: 20.5px; }
  .contact__icon { width: 12px; height: 12px; flex: none; }
</style>
</head>
<body>
  <section class="card card--front" aria-label="Card front">
    <div class="wordmark"><span class="wordmark__square"></span>Quindor &amp; Partners</div>
    <div class="pattern-field" role="img" aria-label="Decorative field of blue, magenta and grey squares"></div>
    <div class="contact">
      <p class="contact__name">Bence Tolnavari</p>
      <p class="contact__title">Managing Director</p>
      <p class="contact__address">1087 Budapest,<br>Tolvenka str. 28/C, Hungary</p>
      <ul class="contact__list">
        <li class="contact__line">
          <svg class="contact__icon" viewBox="0 0 12 12" aria-hidden="true"><path d="M3 1 L5 1 L5.5 3.5 L4.2 4.5 Q5 7 7.5 7.8 L8.5 6.5 L11 7 L11 9 Q10 11 8 10.5 Q2 8.5 1.5 3 Q1.5 1.5 3 1Z" fill="var(--brand-blue)"/></svg>
          +36 30 518 2769
        </li>
        <li class="contact__line">
          <svg class="contact__icon" viewBox="0 0 12 12" aria-hidden="true"><rect x="1" y="2.5" width="10" height="7" fill="none" stroke="var(--brand-blue)" stroke-width="1.2"/><path d="M1 2.5 L6 6.5 L11 2.5" fill="none" stroke="var(--brand-blue)" stroke-width="1.2"/></svg>
          b.tolnavari@quindor.hu
        </li>
        <li class="contact__line">
          <svg class="contact__icon" viewBox="0 0 12 12" aria-hidden="true"><g fill="none" stroke="var(--brand-blue)" stroke-width="1"><circle cx="6" cy="6" r="5"/><ellipse cx="6" cy="6" rx="2.2" ry="5"/><path d="M1 6 H11 M2 3.5 H10 M2 8.5 H10"/></g></svg>
          www.quindor.hu
        </li>
      </ul>
    </div>
  </section>

  <section class="card card--back" aria-label="Card back">
    <div class="wordmark"><span class="wordmark__square"></span>Quindor &amp; Partners</div>
  </section>
</body>
</html>
```